BRN website video quote promotion tiles

We are promoting vehicle leasing by video, which contains several quotation examples imported from the video. We must re-vamp the quotation tiles, contact boxes, and contact form. The first tile is generated from the video, so this must be a separate project. We are looking for a welcoming, professional flow and leave color choices to design with an emphasis on communication prompts, and additional prompts in the design would be welcome.

Target Market(s)

Any Customer interaction from the tile quotes, contact, call, message,

Industry/Entity Type

vehicle leasing

Coding

Coded - Design and coding required

Number of Pages Required

1 page

Colors

Designer to choose colors to be used in the design.

Requirements
Must have
• emphasis on point of contact and visual impact on quote tile excluding main one
Should not have
• changes to the quote structure as these imported from video pricing no changes to main image as this template which can addressed as separate project

```html
<!DOCTYPE html>
<html lang="en">
<head>
<meta charset="utf-8">
<title>BRN Contract Hire Quote Tiles</title>
<link href="https://fonts.googleapis.com/css2?family=Montserrat:wght@300;400;500;700;800;900&family=Oswald:wght@700&family=Playfair+Display:wght@700;900&display=swap" rel="stylesheet">
<style>
:root{
  --ink:#111111;
  --page:#0f0f0f;
  --white:#ffffff;
  --cream:#f8e9c6;
  --cream-light:#fcf6e8;
  --orange:#e08535;
  --orange-deep:#db7a2e;
  --gold:#e9bb42;
  --grey:#777777;
}
*{margin:0;padding:0;box-sizing:border-box}
html,body{width:1200px;height:2626px;overflow:hidden;background:var(--page)}
body{font-family:"Montserrat",sans-serif;color:var(--ink)}
.stage{position:absolute;left:0;top:0;width:1177px;height:2576px;transform:scale(1.0195,1.0194);transform-origin:0 0}
.tile{position:absolute;left:97px;width:983px;height:553px;background:var(--white);overflow:hidden}
.tile--one{top:86px}
.tile--two{top:687px}
.tile--three{top:1311px}
.tile--form{top:1937px}
.tile__bg{position:absolute;left:17px;right:17px;top:14px;bottom:13px;border-radius:4px}
.tile--one .tile__bg{background:linear-gradient(180deg,#fffdf8 0%,var(--cream) 100%)}
.tile--two .tile__bg{background:linear-gradient(90deg,#fff 0%,#fffaf0 50%,var(--cream-light) 100%)}
.tile--two .tile__panel{position:absolute;left:491px;right:17px;top:14px;bottom:13px;background:linear-gradient(180deg,var(--cream) 0%,var(--cream-light) 100%)}
.tile--three .tile__bg{background:radial-gradient(ellipse at 60% 50%,#fffaf0 0%,var(--cream) 70%)}
.tile--form .tile__bg{left:21px;right:21px;top:14px;bottom:14px;background:linear-gradient(180deg,#fcf0d6 0%,#fdf8ee 100%)}
.swoosh{position:absolute;right:0;top:0;width:220px;height:280px}
.accent-bar{position:absolute;left:57px;width:3px;height:58px;background:var(--orange)}
.title{position:absolute;left:70px;line-height:1;white-space:nowrap}
.tile--one .title{top:54px;font-size:56px;font-weight:700;letter-spacing:.5px}
.tile--one .title .light{font-weight:300}
.tile--two .title{top:58px;font-size:61px;font-weight:800;letter-spacing:.5px}
.tile--three .title{top:52px;font-family:"Playfair Display",serif;font-size:50px;font-weight:900;letter-spacing:-1.5px}
.stat{position:absolute;line-height:1;white-space:nowrap}
.stat__num{font-size:60px;font-weight:800;color:var(--orange)}
.stat__label{font-size:21px;font-weight:400;color:var(--ink)}
.tile--three .stat__num{color:var(--ink)}
.tile--three .stat__label{color:var(--grey)}
.service{position:absolute;left:46px;line-height:1;white-space:nowrap}
.tile--one .service{top:274px;font-family:"Oswald",sans-serif;font-size:38px;font-weight:700;letter-spacing:-.3px}
.tile--two .service{top:270px;font-size:46px;font-weight:800;letter-spacing:1px}
.tile--three .service{top:258px;font-family:"Playfair Display",serif;font-size:44px;font-weight:900;letter-spacing:-1.5px}
.band{position:absolute;left:0;top:325px;width:584px;height:48px;background:var(--ink);display:flex;align-items:center;padding-left:46px}
.band__text{font-size:36px;font-weight:800;color:var(--gold);letter-spacing:0;white-space:nowrap}
.band--bright{width:600px;background:linear-gradient(90deg,var(--gold) 0%,#e6a23d 60%,var(--orange-deep) 100%);clip-path:polygon(0 0,98% 0,100% 100%,0 100%)}
.band--bright .band__text{color:var(--ink)}
.btn{position:absolute;top:406px;height:53px;border:2px solid var(--ink);border-radius:27px;display:flex;align-items:center;justify-content:center;font-size:21px;font-weight:800;letter-spacing:.3px;color:var(--ink);white-space:nowrap}
.btn--contact{left:46px;width:237px;background:var(--orange)}
.btn--chat{left:295px;width:289px;background:var(--gold)}
.tile--two .btn,.tile--three .btn{top:412px}
.tile--three .btn{font-family:"Playfair Display",serif;font-weight:900;font-size:20px;letter-spacing:-.8px}
.price{position:absolute;left:665px;top:58px;width:256px;height:256px;border-radius:50%;border:3px solid var(--white);box-shadow:0 22px 40px rgba(60,40,10,.35);text-align:center}
.tile--one .price{background:radial-gradient(circle at 50% 35%,#ebb03f 0%,var(--orange) 70%)}
.tile--two .price{top:57px;background:var(--gold)}
.tile--three .price{background:radial-gradient(circle at 50% 45%,#fff 40%,#fbefd6 100%);border-color:#fbeed4}
.price__currency{position:absolute;left:0;right:0;top:28px;font-size:66px;font-weight:900;line-height:1}
.price__value{position:absolute;left:0;right:0;top:94px;font-size:64px;font-weight:900;line-height:1;letter-spacing:-1px}
.tile--three .price__value{font-family:"Playfair Display",serif;font-weight:700;letter-spacing:-2px;font-size:66px;top:90px}
.price__vat{position:absolute;left:36px;top:171px;width:178px;height:38px;border:2px solid var(--ink);border-radius:19px;background:var(--gold);font-size:23px;font-weight:500;display:flex;align-items:center;justify-content:center}
.tile--two .price__vat{background:transparent}
.tile--three .price__vat{border:none;top:173px}
.form__eyebrow{position:absolute;left:0;right:0;top:64px;text-align:center;font-size:25px;font-weight:400;color:var(--orange);letter-spacing:.5px;line-height:1}
.form__title{position:absolute;left:0;right:0;top:102px;text-align:center;font-size:38px;font-weight:800;letter-spacing:.5px;line-height:1}
.field{position:absolute;background:var(--white);border-radius:26px;box-shadow:0 3px 6px rgba(0,0,0,.12);font-size:11px;letter-spacing:2px;color:#8a8a8a;padding:22px 0 0 33px;line-height:1}
.field--input{left:48px;width:432px;height:52px}
.field--message{left:503px;top:180px;width:432px;height:194px;border-radius:22px;padding-top:24px}
.submit{position:absolute;left:48px;top:400px;width:887px;height:53px;border:2px solid var(--ink);border-radius:27px;background:var(--orange);display:flex;align-items:center;justify-content:center;font-family:"Playfair Display",serif;font-weight:900;font-size:21px;letter-spacing:-1px}
</style>
</head>
<body>
<main class="stage">

  <section class="tile tile--one" aria-label="Contract hire quote">
    <div class="tile__bg"></div>
    <span class="accent-bar" style="top:52px"></span>
    <h2 class="title">CONTRACT <span class="light">HIRE</span></h2>
    <span class="stat stat__num" style="left:63px;top:162px">3</span>
    <span class="stat stat__label" style="left:52px;top:224px">Years</span>
    <span class="stat stat__num" style="left:210px;top:162px">9+35</span>
    <span class="stat stat__num" style="left:440px;top:162px">6K</span>
    <span class="stat stat__label" style="left:407px;top:224px">Miles Annualy</span>
    <p class="service">COMPLTETE SERVICING</p>
    <div class="band"><span class="band__text">&amp; MAINTENECE INCLUDED</span></div>
    <span class="btn btn--contact">CONTACT US</span>
    <span class="btn btn--chat">CHATLINE NOW</span>
    <div class="price">
      <span class="price__currency">£</span>
      <span class="price__value">249.27</span>
      <span class="price__vat">PLUS VAT</span>
    </div>
  </section>

  <section class="tile tile--two" aria-label="Contract hire quote">
    <div class="tile__bg"></div>
    <div class="tile__panel"></div>
    <svg class="swoosh" viewBox="0 0 220 280" aria-hidden="true">
      <defs><linearGradient id="swooshTwo" x1="0" y1="0" x2="1" y2="1"><stop offset="0" stop-color="#e9bb42"/><stop offset="1" stop-color="#e07a2c"/></linearGradient></defs>
      <path d="M0 56 C40 30 70 12 85 0 L220 0 L220 150 C195 200 170 250 140 262 L0 262 Z" fill="url(#swooshTwo)"/>
    </svg>
    <span class="accent-bar" style="top:52px"></span>
    <h2 class="title">CONTRACT HIRE</h2>
    <span class="stat stat__num" style="left:61px;top:160px">3</span>
    <span class="stat stat__label" style="left:105px;top:182px">Years</span>
    <span class="stat stat__num" style="left:185px;top:160px">9+35</span>
    <span class="stat stat__num" style="left:353px;top:160px">6K</span>
    <span class="stat stat__label" style="left:433px;top:183px">Miles Annualy</span>
    <p class="service">COMPLTETE SERVICING</p>
    <div class="band"><span class="band__text">&amp; MAINTENECE INCLUDED</span></div>
    <span class="btn btn--contact">CONTACT US</span>
    <span class="btn btn--chat">CHATLINE NOW</span>
    <div class="price">
      <span class="price__currency">£</span>
      <span class="price__value">249.27</span>
      <span class="price__vat">PLUS VAT</span>
    </div>
  </section>

  <section class="tile tile--three" aria-label="Contract hire quote">
    <div class="tile__bg"></div>
    <svg class="swoosh" viewBox="0 0 220 280" aria-hidden="true">
      <defs><linearGradient id="swooshThree" x1="0" y1="0" x2="1" y2="1"><stop offset="0" stop-color="#e9bb42"/><stop offset="1" stop-color="#e07a2c"/></linearGradient></defs>
      <path d="M0 56 C40 30 70 12 85 0 L220 0 L220 150 C195 200 170 250 140 262 L0 262 Z" fill="url(#swooshThree)"/>
    </svg>
    <span class="accent-bar" style="top:52px"></span>
    <h2 class="title">CONTRACT HIRE</h2>
    <span class="stat stat__num" style="left:61px;top:162px">3</span>
    <span class="stat stat__label" style="left:105px;top:183px">Years</span>
    <span class="stat stat__num" style="left:185px;top:162px">9+35</span>
    <span class="stat stat__num" style="left:353px;top:162px">6K</span>
    <span class="stat stat__label" style="left:433px;top:184px">Miles Annualy</span>
    <p class="service">COMPLTETE SERVICING</p>
    <div class="band band--bright"><span class="band__text">&amp; MAINTENECE INCLUDED</span></div>
    <span class="btn btn--contact">CONTACT US</span>
    <span class="btn btn--chat">CHATLINE NOW</span>
    <div class="price">
      <span class="price__currency">£</span>
      <span class="price__value">249.27</span>
      <span class="price__vat">PLUS VAT</span>
    </div>
  </section>

  <section class="tile tile--form" aria-label="Contact form">
    <div class="tile__bg"></div>
    <p class="form__eyebrow">PLEASE SUBMIT</p>
    <h2 class="form__title">YOUR CONTACT DETAILS</h2>
    <div class="field field--input" style="top:180px">YOUR NAME</div>
    <div class="field field--input" style="top:252px">EMAIL ADDRESS</div>
    <div class="field field--input" style="top:324px">MOBILE NUMBER</div>
    <div class="field field--message">MESSAGE</div>
    <span class="submit">SUBMIT NOW</span>
  </section>

</main>
</body>
</html>
```